RevelHubQZ Business Cards

Front
Has logo with a design. Website address (www.revelhubqz-example.net)
Has slogan (discover the nightlife)
Has phone number (5182297734)
Should be bold and stands out.

Back
Has details about what we offer.

Events
Search upcoming events
Submit events
Party Image Gallery
View and download HQ party images
Sign up as a contributing event photographer and get paid!
Tickets
Sell your event tickets online for free!
Direct pay
No ticket fee

Target Market(s)

These cards will be handed out in clubs and events to patrons.

Industry/Entity Type

Business

Contact Information for Business Card

Should match or mirror our website in some sort of way. Visit the website to get ideas.

Requirements
Must have
• Must be designed for a 3x3 inch card.

```html
<!DOCTYPE html>
<html lang="en">
<head>
<meta charset="utf-8">
<title>RevelHubQZ Business Cards</title>
<link href="https://fonts.googleapis.com/css2?family=Questrial&family=Mulish:wght@700;800&display=swap" rel="stylesheet">
<style>
  :root {
    --stage: #e0e0de;
    --card: #f9f9f9;
    --ink: #2a2a2a;
    --blue: #1ba9e1;
    --pink: #e0418d;
  }
  * { margin: 0; padding: 0; box-sizing: border-box; }
  html, body { width: 1200px; height: 659px; overflow: hidden; background: var(--stage); }
  .canvas { position: relative; width: 1200px; height: 659px; }
  .card {
    position: absolute; top: 143px; width: 375px; height: 374px;
    background: var(--card); overflow: hidden;
    font-family: "Questrial", sans-serif; color: var(--ink);
  }
  .card--front { left: 201px; }
  .card--back { left: 624px; }

  .brand { position: absolute; left: 27px; top: 54px; display: flex; align-items: center; gap: 10px; }
  .brand__dot { width: 40px; height: 40px; border-radius: 50%; background: var(--blue); }
  .brand__name { font-size: 31px; line-height: 1; color: var(--blue); font-family: "Questrial", sans-serif; }
  .brand__slogan {
    position: absolute; left: 77px; top: 104px;
    font-size: 10.5px; letter-spacing: 5.2px; color: var(--ink);
  }

  .contact { position: absolute; left: 27px; top: 195px; }
  .contact__name { font-family: "Mulish", sans-serif; font-weight: 800; font-size: 21px; line-height: 1.2; }
  .contact__role { font-size: 12px; margin-top: 2px; }
  .contact__lines { margin-top: 19px; font-size: 14px; line-height: 18.5px; }
  .accent-blue { color: var(--blue); }
  .accent-pink { color: var(--pink); }

  .offer__title {
    position: absolute; top: 44px; left: 0; width: 100%; text-align: center;
    font-family: "Mulish", sans-serif; font-weight: 800; font-size: 16px; color: var(--pink);
  }
  .offer__list {
    position: absolute; top: 80px; left: 0; width: 100%; list-style: none;
    text-align: center; font-size: 14.5px; line-height: 21.6px;
  }

  .eq-band {
    position: absolute; left: 0; bottom: 0; width: 100%; height: 33px;
    background: linear-gradient(to bottom, var(--pink) 0%, var(--pink) 30%, var(--blue) 45%, var(--blue) 100%);
    opacity: 0.9;
  }
</style>
</head>
<body>
<div class="canvas">
  <section class="card card--front">
    <div class="brand">
      <span class="brand__dot"></span>
      <span class="brand__name">RevelHubQZ</span>
    </div>
    <p class="brand__slogan">discover the nightlife</p>

    <div class="contact">
      <h1 class="contact__name">Mara Ellison</h1>
      <p class="contact__role">Managing Director</p>
      <p class="contact__lines">
        5182297734<br>
        support@revelhubqz-example.net<br>
        www.<span class="accent-blue">revelhub</span><span class="accent-pink">qz</span>-example.net
      </p>
    </div>
    <div class="eq-band" role="img" aria-label="Pink and blue equalizer bar pattern"></div>
  </section>

  <section class="card card--back">
    <h2 class="offer__title">WE OFFER</h2>
    <ul class="offer__list">
      <li>Events</li>
      <li>Search upcoming events</li>
      <li>Submit events</li>
      <li>Party Image Gallery</li>
      <li>View and download HQ party images</li>
      <li>Sign up as a contributing event<br>photographer and get paid!</li>
      <li>Tickets</li>
      <li>Sell your event tickets online for free!</li>
      <li>Direct pay</li>
      <li>No ticket fee</li>
    </ul>
    <div class="eq-band" role="img" aria-label="Pink and blue equalizer bar pattern"></div>
  </section>
</div>
</body>
</html>
```